Business Card Design

We need a business card designed for our new company. Prefer a black card with white logo & writing.

Contact Information for Business Card

Ted Galloway, address: 7-4812 Fernhollow Road, Abbotsford, BC, V3K 8R2, Office Phone: 604-712-3390, Cell: 604-947-2164, Email: ted@resinworkshub.ca

Colors

Designer to choose only greyscale colors for use in the design.

```html
<!DOCTYPE html>
<html lang="en">
<head>
<meta charset="utf-8">
<title>Resinworks Hub – Business Card</title>
<link href="https://fonts.googleapis.com/css2?family=Poppins:wght@300;400;700&display=swap" rel="stylesheet">
<style>
  :root {
    --backdrop: #1c1c1e;
    --card: #222225;
    --ink: #f4f4f4;
    --ink-soft: #cfcfcf;
    --foil-tone: #3a3a3e;
    --emboss: #0f0f10;
  }
  * { margin: 0; padding: 0; box-sizing: border-box; }
  html, body { width: 1200px; height: 780px; overflow: hidden; }
  body {
    background: var(--backdrop);
    font-family: "Poppins", sans-serif;
    color: var(--ink);
    position: relative;
  }
  .card {
    position: absolute;
    top: 235px;
    width: 540px;
    height: 310px;
    background: var(--card);
    border-radius: 4px;
    box-shadow: 0 18px 40px rgba(0,0,0,.55);
    overflow: hidden;
  }
  .card--front { left: 40px; }
  .card--back { left: 620px; }

  .brand {
    display: flex;
    align-items: center;
    gap: 10px;
    font-weight: 700;
    letter-spacing: .5px;
    text-transform: uppercase;
  }
  .brand__mark {
    width: 14px; height: 14px;
    background: var(--ink);
  }
  .card--front .brand {
    position: absolute;
    left: 34px; top: 34px;
    font-size: 24px;
  }

  .contact {
    position: absolute;
    left: 34px; top: 100px;
    font-size: 12.5px;
    font-weight: 300;
    line-height: 1.55;
    color: var(--ink-soft);
    list-style: none;
  }
  .contact__address { margin-bottom: 8px; }
  .contact__item { display: flex; align-items: center; gap: 9px; }
  .contact__icon { width: 11px; height: 11px; flex: none; }

  .foil-area {
    position: absolute;
    right: 0; bottom: 0;
    width: 250px; height: 120px;
    background: linear-gradient(135deg, var(--card) 0%, var(--foil-tone) 100%);
  }

  .person {
    position: absolute;
    right: 34px; bottom: 30px;
    text-align: right;
  }
  .person__name { font-size: 30px; font-weight: 300; line-height: 1.1; }
  .person__first { font-weight: 700; }
  .person__role { font-size: 15px; font-weight: 300; }

  .card--back .brand {
    position: absolute;
    inset: 0;
    justify-content: center;
    font-size: 32px;
    color: var(--emboss);
  }
  .card--back .brand__mark { background: var(--emboss); width: 18px; height: 18px; }
</style>
</head>
<body>

  <section class="card card--front" aria-label="Business card front">
    <div class="brand"><span class="brand__mark"></span>Resinworks Hub</div>

    <ul class="contact">
      <li class="contact__address">7-4812 Fernhollow Road,<br>Abbotsford, BC, V3K 8R2.</li>
      <li class="contact__item">
        <svg class="contact__icon" viewBox="0 0 12 12" aria-hidden="true"><path d="M2 1h2.5l1 3-1.5 1a6 6 0 0 0 3 3l1-1.5 3 1V11A10 10 0 0 1 1 2z" fill="currentColor"/></svg>
        604-712-3390
      </li>
      <li class="contact__item">
        <svg class="contact__icon" viewBox="0 0 12 12" aria-hidden="true"><rect x="3" y="0.5" width="6" height="11" rx="1" fill="none" stroke="currentColor"/><circle cx="6" cy="9.5" r=".7" fill="currentColor"/></svg>
        604-947-2164
      </li>
      <li class="contact__item">
        <svg class="contact__icon" viewBox="0 0 12 12" aria-hidden="true"><circle cx="6" cy="6" r="5" fill="none" stroke="currentColor"/><path d="M1 6h10M6 1c-3 3-3 7 0 10M6 1c3 3 3 7 0 10" fill="none" stroke="currentColor" stroke-width=".8"/></svg>
        www.resinworkshub.ca
      </li>
      <li class="contact__item">
        <svg class="contact__icon" viewBox="0 0 12 12" aria-hidden="true"><rect x=".5" y="2" width="11" height="8" fill="none" stroke="currentColor"/><path d="M.5 2 6 7l5.5-5" fill="none" stroke="currentColor"/></svg>
        ted@resinworkshub.ca
      </li>
    </ul>

    <div class="foil-area" role="img" aria-label="Area for a glossy foil mountain illustration"></div>

    <div class="person">
      <p class="person__name"><span class="person__first">Ted</span> Galloway</p>
      <p class="person__role">owner</p>
    </div>
  </section>

  <section class="card card--back" aria-label="Business card back">
    <div class="brand"><span class="brand__mark"></span>Resinworks Hub</div>
  </section>

</body>
</html>
```